Ledgers On Track Business Card Design

We are a bookkeeping and accounting practice and are particularly passionate about Vantu as 'state of the art' accounting software. We offer a number of services which are listed on the back of the card. The logos for LOT have already been developed. There are also other logos of organisations we are involved with - Vantu (both certified advisor and silver partner), QAG, and filenow hub. Regarding colours, we would like to use the colours similar to our website, www.ledgersontrack.com, and these connect with the www.vantu.com.au website. The proposed layout as it is just does not look too great - it looks like an amateur has done it - which is true!

Industry/Entity Type

Accounting

Contact Information for Business Card

The details to appear on the card are found on the files uploaded. I have front and back rough layouts.

```html
<!DOCTYPE html>
<html lang="en">
<head>
<meta charset="utf-8">
<title>Ledgers On Track – Business Card</title>
<link href="https://fonts.googleapis.com/css2?family=Bree+Serif&family=Crimson+Text:wght@400;600;700&display=swap" rel="stylesheet">
<style>
  :root{
    --brand-blue:#4a5f9c;
    --band-blue:#4d62a0;
    --tick-green:#5aac44;
    --name-green:#5aa046;
    --ink:#333a44;
    --grey:#6b6f76;
    --badge-light:#c9d3e6;
    --badge-mid:#9aa9c9;
    --badge-grey:#c4c6ca;
    --card:#ffffff;
    --page:#e9e6e1;
  }
  *{box-sizing:border-box;margin:0;padding:0}
  html,body{width:1200px;height:1023px;overflow:hidden}
  body{background:var(--page);position:relative;font-family:"Crimson Text",Georgia,serif;color:var(--ink)}

  .card{position:absolute;width:700px;height:400px;background:var(--card);box-shadow:0 6px 18px rgba(0,0,0,.18);overflow:hidden}
  .card--back{left:140px;top:70px}
  .card--front{left:360px;top:550px}

  .wordmark{font-family:"Bree Serif",Georgia,serif;color:var(--brand-blue);font-weight:400;display:flex;align-items:center;gap:14px;white-space:nowrap}
  .wordmark__dot{width:22px;height:22px;border-radius:50%;background:var(--tick-green);flex:none}

  /* back */
  .card--back .wordmark{position:absolute;left:46px;top:24px;font-size:50px}
  .services-band{position:absolute;left:0;top:100px;width:100%;height:238px;background:var(--band-blue)}
  .services{list-style:none;position:absolute;left:46px;top:114px;color:#fff}
  .services li{display:flex;align-items:center;font-size:21px;line-height:30px;white-space:nowrap}
  .services svg{width:16px;height:16px;margin-right:10px;flex:none}
  .services strong{font-weight:700}
  .services span{font-weight:400;opacity:.92}
  .back-badges{position:absolute;right:30px;top:266px;display:flex;gap:6px}
  .back-badges .badge{width:58px;height:58px}
  .card--back .partner-name{position:absolute;left:46px;bottom:16px}

  .partner-name{font-family:"Crimson Text",Georgia,serif;font-size:21px;font-weight:400;color:var(--grey);white-space:nowrap}

  .badge{border-radius:50%}
  .badge--primary{background:var(--badge-light)}
  .badge--silver{background:var(--badge-grey)}
  .badge--advisor{background:var(--badge-mid)}

  /* front */
  .card--front .wordmark{position:absolute;left:46px;top:52px;font-size:58px}
  .abn{position:absolute;left:70px;top:126px;font-size:13px;color:var(--grey);letter-spacing:.3px}
  .card--front .partner-name{position:absolute;left:58px;top:182px}
  .contacts{list-style:none;position:absolute;left:60px;top:234px}
  .contacts li{display:flex;align-items:center;font-size:19px;line-height:26px;color:var(--ink);white-space:nowrap}
  .contacts svg{width:17px;height:17px;margin-right:12px;flex:none}
  .person{position:absolute;right:96px;top:168px;text-align:center}
  .person__name{font-size:33px;font-weight:700;color:var(--name-green);line-height:1}
  .person__role{font-size:18px;color:var(--grey);line-height:22px;margin-top:6px}
  .front-badges{position:absolute;right:92px;top:260px;display:flex;gap:12px}
  .front-badges .badge{width:82px;height:82px}
  .address-bar{position:absolute;left:0;bottom:0;width:100%;height:38px;background:var(--band-blue);color:#fff;font-size:19px;display:flex;align-items:center;justify-content:center}
</style>
</head>
<body>

<section class="card card--back" aria-label="Card back – services">
  <div class="wordmark"><span class="wordmark__dot"></span>Ledgers On Track</div>
  <div class="services-band"></div>
  <ul class="services">
    <li><svg viewBox="0 0 16 16"><path d="M2 9l4 4 8-10" fill="none" stroke="#5aac44" stroke-width="3" stroke-linecap="round" stroke-linejoin="round"/></svg><strong>Bookkeeping</strong>&nbsp;<span>- data entry, bank reconciliation and review</span></li>
    <li><svg viewBox="0 0 16 16"><path d="M2 9l4 4 8-10" fill="none" stroke="#5aac44" stroke-width="3" stroke-linecap="round" stroke-linejoin="round"/></svg><strong>Payroll</strong>&nbsp;<span>- Vantu Payroll Specialist</span></li>
    <li><svg viewBox="0 0 16 16"><path d="M2 9l4 4 8-10" fill="none" stroke="#5aac44" stroke-width="3" stroke-linecap="round" stroke-linejoin="round"/></svg><strong>BAS</strong>&nbsp;<span>- QAG Public BAS Practitioner</span></li>
    <li><svg viewBox="0 0 16 16"><path d="M2 9l4 4 8-10" fill="none" stroke="#5aac44" stroke-width="3" stroke-linecap="round" stroke-linejoin="round"/></svg><strong>Training &amp; support</strong>&nbsp;<span>- Vantu Certified Advisor</span></li>
    <li><svg viewBox="0 0 16 16"><path d="M2 9l4 4 8-10" fill="none" stroke="#5aac44" stroke-width="3" stroke-linecap="round" stroke-linejoin="round"/></svg><strong>Management reports</strong></li>
    <li><svg viewBox="0 0 16 16"><path d="M2 9l4 4 8-10" fill="none" stroke="#5aac44" stroke-width="3" stroke-linecap="round" stroke-linejoin="round"/></svg><strong>Tax</strong>&nbsp;<span>- filenow hub Member</span></li>
    <li><svg viewBox="0 0 16 16"><path d="M2 9l4 4 8-10" fill="none" stroke="#5aac44" stroke-width="3" stroke-linecap="round" stroke-linejoin="round"/></svg><strong>HR services</strong></li>
  </ul>
  <div class="back-badges">
    <div class="badge badge--primary" role="img" aria-label="Vantu partner badge"></div>
    <div class="badge badge--silver" role="img" aria-label="Vantu silver partner badge"></div>
  </div>
  <div class="partner-name">QAG Quorum Accountants Guild</div>
</section>

<section class="card card--front" aria-label="Card front – contact details">
  <div class="wordmark"><span class="wordmark__dot"></span>Ledgers On Track</div>
  <div class="abn">ABN 00 123 456 789</div>
  <div class="partner-name">QAG Quorum Accountants Guild</div>
  <ul class="contacts">
    <li><svg viewBox="0 0 17 17"><rect width="17" height="17" rx="3" fill="#5aac44"/><path d="M4 6c0-1 1-2 2-2h5c1 0 2 1 2 2v1H10V6H7v1H4z M5 8h7l1 5H4z" fill="#fff"/></svg>03 9000 4127</li>
    <li><svg viewBox="0 0 17 17"><rect width="17" height="17" rx="3" fill="#5aac44"/><rect x="5.5" y="3" width="6" height="11" rx="1" fill="#fff"/><rect x="6.5" y="4.5" width="4" height="6" fill="#5aac44"/></svg>0400 555 318</li>
    <li><svg viewBox="0 0 17 17"><rect width="17" height="17" rx="3" fill="#5aac44"/><rect x="3" y="5" width="11" height="8" fill="#fff"/><path d="M3 5l5.5 4.5L14 5" fill="none" stroke="#5aac44" stroke-width="1.2"/></svg>martin@ledgersontrack.com</li>
    <li><svg viewBox="0 0 17 17"><rect width="17" height="17" rx="3" fill="#5aac44"/><circle cx="8.5" cy="8.5" r="5" fill="none" stroke="#fff" stroke-width="1.3"/><ellipse cx="8.5" cy="8.5" rx="2.2" ry="5" fill="none" stroke="#fff" stroke-width="1.1"/><path d="M3.5 8.5h10" stroke="#fff" stroke-width="1.1"/></svg>www.ledgersontrack.com</li>
  </ul>
  <div class="person">
    <div class="person__name">Martin Colby</div>
    <div class="person__role">B Comm MA PhD AQAG<br>Registered BAS agent</div>
  </div>
  <div class="front-badges">
    <div class="badge badge--primary" role="img" aria-label="Vantu partner badge"></div>
    <div class="badge badge--advisor" role="img" aria-label="Vantu certified advisor badge"></div>
  </div>
  <div class="address-bar">18 Harwood Lane, Eltham Park VIC 3095</div>
</section>

</body>
</html>
```